GUARANTEE PAY GIFT CARD DESIGN

This is a GIFT BONUS CARD

SIZE: 3.5INCH x 2INCH, 8.9cm x 5.1cm, DOUBLE SIDE
Orange must be used as an accent or primary colour.
#F37021, CMYK 0, 54, 86, 5

"BONUS CARD" AND "$20" MUST BE PART OF THE DESIGN.

Please see the attached logo
DO NOT use ribbons or gift box illustrations in the design.

***Terms and conditions must be on the back side of the card-
"No Cash Value. Card valid from 1/2/2024 to 3/31/2024. Valid for Brookvale location only. Valid for Dine-in only. Not valid for online togo, delivery, or special events. "

Target Market(s)

40-60 YEARS OLD

Industry/Entity Type

Modern casual malaysian restaurant

Requirements
Must have
• ORANGE COLOUR, BONUS CARD, $20
Should not have
• Ribbons, gift box, CHOPSTICKS, BOWL, NOODLES, CHARATER ILLUSTRATIONS.

```html
<!DOCTYPE html>
<html lang="en">
<head>
<meta charset="utf-8">
<title>Lumo Kitchen Bonus Card</title>
<link rel="stylesheet" href="https://fonts.googleapis.com/css2?family=Montserrat:wght@300;500;700;900&family=Lato:wght@400;700&display=swap">
<style>
  :root {
    --stage: #2a2a2a;
    --card-orange: #f7983a;
    --accent-soft: #e8742a;
    --accent-deep: #d9602a;
    --ink: #111111;
    --badge-black: #0d0d0d;
  }
  * { box-sizing: border-box; margin: 0; padding: 0; }
  html, body { width: 1200px; height: 875px; overflow: hidden; }
  body {
    background: var(--stage);
    font-family: "Montserrat", sans-serif;
    color: var(--ink);
    position: relative;
  }
  .card {
    position: absolute;
    top: 283px;
    width: 540px;
    height: 309px;
    background: var(--card-orange);
    border-radius: 24px;
    overflow: hidden;
  }
  .card--back { left: 40px; }
  .card--front { left: 620px; }

  /* back side */
  .brand-lockup {
    position: absolute;
    left: 0; right: 0; top: 92px;
    display: flex; align-items: center; justify-content: center; gap: 14px;
  }
  .brand-dot {
    width: 22px; height: 22px; border-radius: 50%;
    background: var(--ink);
  }
  .brand-name {
    font-weight: 500;
    font-size: 40px;
    letter-spacing: 4px;
    text-transform: uppercase;
    line-height: 1;
  }
  .brand-tagline {
    position: absolute; left: 0; right: 0; top: 148px;
    text-align: center;
    font-weight: 500; font-size: 11px; letter-spacing: 3px;
    text-transform: uppercase;
  }
  .terms {
    position: absolute; left: 30px; right: 30px; bottom: 34px;
    text-align: center;
    font-family: "Lato", sans-serif;
    font-size: 10.5px; line-height: 1.45;
  }

  /* front side */
  .feature-art {
    position: absolute; left: 0; top: 0; bottom: 0;
    width: 210px;
    background: linear-gradient(160deg, var(--accent-soft), var(--accent-deep));
  }
  .value-badge {
    position: absolute; left: 393px; top: 33px;
    width: 124px; height: 124px; border-radius: 50%;
    background: var(--badge-black);
    display: flex; align-items: center; justify-content: center;
    color: var(--card-orange);
  }
  .value-badge .currency { font-size: 26px; font-weight: 900; margin-top: 14px; margin-right: 2px; }
  .value-badge .amount { font-size: 60px; font-weight: 900; letter-spacing: -2px; }
  .offer {
    position: absolute; left: 232px; top: 150px;
  }
  .offer-brand {
    display: inline-block;
    border: 1.5px solid var(--ink);
    padding: 3px 8px 2px;
  }
  .offer-brand .name {
    display: block;
    font-weight: 700; font-size: 17px; letter-spacing: 1px;
    text-transform: uppercase; line-height: 1.05;
  }
  .offer-brand .tagline {
    display: block; text-align: right;
    font-weight: 700; font-size: 6px; letter-spacing: 1px;
    text-transform: uppercase;
  }
  .offer-title {
    font-weight: 900; font-size: 52px; line-height: 1;
    text-transform: uppercase; margin-top: 4px;
  }
  .offer-sub {
    display: flex; align-items: center; gap: 10px;
    font-weight: 300; font-size: 34px; letter-spacing: 8px;
    text-transform: uppercase; line-height: 1;
  }
  .offer-sub .rules { display: flex; flex-direction: column; gap: 6px; }
  .offer-sub .rules span { display: block; height: 1px; background: var(--ink); }
  .offer-sub .rules .rule-long { width: 70px; }
  .offer-sub .rules .rule-mid { width: 50px; }
  .offer-sub .rules .rule-short { width: 34px; }
</style>
</head>
<body>
  <section class="card card--back" aria-label="Card back">
    <div class="brand-lockup">
      <span class="brand-dot"></span>
      <span class="brand-name">Lumo Kitchen</span>
    </div>
    <p class="brand-tagline">Malaysian Street Food</p>
    <p class="terms">No Cash Value. Card valid from 1/2/2024 to 3/31/2024. Valid for Brookvale location only.<br>Valid for Dine-in only. Not valid for online togo, delivery, or special events.</p>
  </section>

  <section class="card card--front" aria-label="Card front">
    <div class="feature-art" role="img" aria-label="Decorative gift artwork area"></div>
    <div class="value-badge"><span class="currency">$</span><span class="amount">20</span></div>
    <div class="offer">
      <div class="offer-brand">
        <span class="name">Lumo Kitchen</span>
        <span class="tagline">Malaysian Street Food</span>
      </div>
      <div class="offer-title">Bonus</div>
      <div class="offer-sub">Card
        <span class="rules"><span class="rule-long"></span><span class="rule-mid"></span><span class="rule-short"></span></span>
      </div>
    </div>
  </section>
</body>
</html>
```